High-end law practice specializing in closely held business succession planning and complex estates

Solo practitioner whose practice specializes in high-net worth, complex estate planning needs muliple versions of letterhead black and white, please. Letterhead should incorporate slogan, "Protecting your family business is my business," for one and "Complex Estate Planning"; third with no slogan. All for The Law Office of Marcy Lynn Pettibone, PC, 418 Cedar Hollow Ln., Newport News, Virginia 23648, Tel. 757-555-0142 Fax tbd email: marcy@mlplawgroup.example; Marcy Lynn Pettibone, Esq., principal, licensed in VA, NY, DC
Updates

Project Deadline Extended
Reason: My internet service went down and I can only view designs on my smart phone -- it's just too hard to review. So sorry! Working with my ISP now. Please be patient!

Target Market(s)

High net worth clients with complex estate planning needs, family businesses, family farmers, family foresters -- people with unique estate/succession planning needs who need a specialist who understands them.

Industry/Entity Type

Business

Font styles to use
Script

Requirements
Must have
• A high-end look and feel, connoting trustworthiness, special knowledge, and expertise.

```html
<!DOCTYPE html>
<html lang="en">
<head>
<meta charset="utf-8">
<title>Marcy Lynn Pettibone, Esq. — Letterhead</title>
<link rel="stylesheet" href="https://fonts.googleapis.com/css2?family=Arimo:wght@400;700&display=swap">
<style>
  :root {
    --paper: #fdfdfd;
    --ink: #2b2b2b;
    --ink-soft: #3c3c3c;
    --band: #7b7b7b;
    --band-text: #ffffff;
    --icon-tone: #d9d9d9;
  }
  html, body {
    margin: 0;
    padding: 0;
    overflow: hidden;
    background: var(--paper);
  }
  .letterhead {
    position: relative;
    width: 849px;
    height: 1200px;
    background: var(--paper);
    font-family: "Arimo", Arial, sans-serif;
    color: var(--ink);
    overflow: hidden;
  }
  .brand-square {
    position: absolute;
    left: 0;
    top: 129px;
    width: 37px;
    height: 26px;
    background: var(--band);
  }
  .practitioner-name {
    position: absolute;
    left: 49px;
    top: 127px;
    margin: 0;
    font-size: 27px;
    font-weight: 700;
    color: var(--ink);
    letter-spacing: -0.2px;
    white-space: nowrap;
  }
  .credentials {
    position: absolute;
    left: 49px;
    top: 163px;
    margin: 0;
    font-size: 19px;
    line-height: 31px;
    color: var(--ink-soft);
  }
  .practice-icons {
    position: absolute;
    left: 405px;
    top: 66px;
    width: 420px;
    height: 44px;
    background: linear-gradient(90deg, var(--icon-tone), #e6e6e6, var(--icon-tone));
    border-radius: 3px;
  }
  .slogan-band {
    position: absolute;
    left: 375px;
    top: 128px;
    width: 469px;
    height: 27px;
    background: var(--band);
    color: var(--band-text);
    font-size: 19px;
    line-height: 27px;
    text-align: right;
    padding-right: 16px;
    box-sizing: border-box;
    margin: 0;
  }
  .contact-footer {
    position: absolute;
    left: 0;
    width: 849px;
    top: 1115px;
    text-align: center;
    font-size: 16px;
    color: var(--ink-soft);
  }
  .contact-line {
    margin: 0;
    height: 28px;
    line-height: 24px;
    white-space: nowrap;
  }
  .contact-item {
    display: inline-flex;
    align-items: center;
    gap: 4px;
    margin: 0 6px;
  }
  .contact-icon {
    width: 18px;
    height: 18px;
    fill: none;
    stroke: var(--ink-soft);
    stroke-width: 1.2;
  }
</style>
</head>
<body>
<main class="letterhead">
  <div class="brand-square"></div>
  <h1 class="practitioner-name">Marcy Lynn Pettibone</h1>
  <p class="credentials">Esq., principal,<br>licensed in VA, NY, DC</p>

  <div class="practice-icons" role="img" aria-label="Row of practice-area icons: oath, justice, gavel, scales, documents, family, passport, handshake"></div>
  <p class="slogan-band">Protecting your family business is my business.</p>

  <footer class="contact-footer">
    <p class="contact-line">
      <span class="contact-item">
        <svg class="contact-icon" viewBox="0 0 18 18" aria-hidden="true"><path d="M9 16s-5-5.2-5-9a5 5 0 0 1 10 0c0 3.8-5 9-5 9z"/><circle cx="9" cy="7" r="1.8"/></svg>
        PC, 418 Cedar Hollow Ln., Newport News, Virginia 23648,
      </span>
    </p>
    <p class="contact-line">
      <span class="contact-item">
        <svg class="contact-icon" viewBox="0 0 18 18" aria-hidden="true"><path d="M2 7c2-3 12-3 14 0l-1.5 1.5-2.5-1V6H6v1.5l-2.5 1z"/><rect x="5" y="10" width="8" height="5" rx="1"/></svg>
        757-555-0142
      </span>
      <span class="contact-item">
        <svg class="contact-icon" viewBox="0 0 18 18" aria-hidden="true"><rect x="5" y="2" width="8" height="5"/><rect x="2" y="7" width="14" height="6" rx="1"/><rect x="5" y="11" width="8" height="5"/></svg>
        757-555-0199
      </span>
      <span class="contact-item">
        <svg class="contact-icon" viewBox="0 0 18 18" aria-hidden="true"><rect x="2" y="4" width="14" height="10"/><path d="M2 4l7 6 7-6"/></svg>
        marcy@mlplawgroup.example
      </span>
      <span class="contact-item">
        <svg class="contact-icon" viewBox="0 0 18 18" aria-hidden="true"><circle cx="9" cy="9" r="7"/><ellipse cx="9" cy="9" rx="3" ry="7"/><path d="M2 9h14"/></svg>
        www.mlplawgroup.example
      </span>
    </p>
  </footer>
</main>
</body>
</html>
```